Business Card - connecting 2 souls and beggining the journey of self discovery

Logo on the front
with tag line

On the back list of services and contact details

Seminars
workshops
Coaching
podcasts

Darren Whitlow
Health & Wellbeing Life Coach
0491 372 615
darren@brightcoreliving.example
brightcoreliving.example

Industry/Entity Type

Life Coaching

Contact Information for Business Card

I like the use of colour from the logo to be used. I'm not a fan of white.

Requirements
Must have
• My tagline: Your path to balance begins within
Nice to have
• Use of colour that is in the mind body soul logo

```html
<!DOCTYPE html>
<html lang="en">
<head>
<meta charset="utf-8">
<title>Brightcore Living – Business Card</title>
<link href="https://fonts.googleapis.com/css2?family=Roboto:wght@400;500&display=swap" rel="stylesheet">
<style>
  :root {
    --page-bg: #e9e6e2;
    --card-bg: #333232;
    --accent: #f0914a;
    --text-light: #ffffff;
    --mark: #e9a23f;
  }
  * { box-sizing: border-box; margin: 0; padding: 0; }
  html, body { width: 1200px; height: 1200px; overflow: hidden; }
  body {
    background: var(--page-bg);
    font-family: "Roboto", Arial, sans-serif;
    position: relative;
  }
  .card {
    position: absolute;
    left: 213px;
    width: 774px;
    height: 440px;
    background: var(--card-bg);
    border-radius: 20px;
    overflow: hidden;
    box-shadow: 0 6px 14px rgba(0,0,0,0.25);
  }
  .card--front { top: 150px; }
  .card--back { top: 634px; }

  .person { position: absolute; left: 49px; top: 117px; color: var(--text-light); }
  .person__name { color: var(--accent); font-size: 30px; font-weight: 500; line-height: 1.1; }
  .person__role { font-size: 20px; margin-top: 8px; }
  .address { font-size: 19px; line-height: 1.38; margin-top: 25px; }
  .contacts { list-style: none; margin-top: 20px; font-size: 19px; }
  .contacts li { display: flex; align-items: center; gap: 7px; height: 27.5px; }
  .contacts svg { width: 18px; height: 18px; flex: none; }

  .brand { position: absolute; display: flex; flex-direction: column; align-items: center; color: var(--text-light); }
  .brand__dot { border-radius: 50%; background: var(--mark); }
  .brand__name { font-weight: 400; letter-spacing: -0.5px; white-space: nowrap; }
  .card--front .brand { left: 427px; top: 31px; width: 320px; }
  .card--front .brand__dot { width: 100px; height: 100px; }
  .card--front .brand__name { font-size: 27px; margin-top: 20px; }
  .card--back .brand { left: 0; right: 0; top: 98px; }
  .card--back .brand__dot { width: 128px; height: 128px; }
  .card--back .brand__name { font-size: 33px; margin-top: 30px; }

  .services {
    position: absolute; left: 0; right: 0; bottom: 0; height: 36px;
    background: var(--accent); color: var(--text-light);
    display: flex; align-items: center; padding-left: 44px;
    font-size: 19px; list-style: none;
  }
  .services li + li::before {
    content: ""; display: inline-block; width: 8px; height: 8px; border-radius: 50%;
    background: var(--text-light); margin: 0 9px 2px 9px; vertical-align: middle;
  }
  .tagline {
    position: absolute; left: 0; right: 0; top: 380px; text-align: center;
    color: var(--accent); font-size: 23px;
  }
</style>
</head>
<body>
  <section class="card card--front">
    <div class="person">
      <h1 class="person__name">Darren Whitlow</h1>
      <p class="person__role">Health &amp; Wellbeing Life Coach</p>
      <p class="address">2280 Larkspur Avenue, Suite 410<br>Fairmont, CA 3061</p>
      <ul class="contacts">
        <li><svg viewBox="0 0 24 24" fill="none" stroke="#f0914a" stroke-width="1.6"><path d="M5 3h4l2 5-2.5 1.5a11 11 0 0 0 6 6L16 13l5 2v4a2 2 0 0 1-2 2A17 17 0 0 1 3 5a2 2 0 0 1 2-2z"/></svg>0491 372 615</li>
        <li><svg viewBox="0 0 24 24" fill="none" stroke="#f0914a" stroke-width="1.6"><rect x="7" y="2" width="10" height="20" rx="2"/><line x1="11" y1="18.5" x2="13" y2="18.5"/></svg>000-000-0000</li>
        <li><svg viewBox="0 0 24 24" fill="none" stroke="#f0914a" stroke-width="1.6"><rect x="3" y="5" width="18" height="14"/><path d="M3 5l9 8 9-8M3 19l7-7M21 19l-7-7"/></svg>darren@brightcoreliving.example</li>
        <li><svg viewBox="0 0 24 24" fill="none" stroke="#f0914a" stroke-width="1.6"><circle cx="12" cy="12" r="9"/><ellipse cx="12" cy="12" rx="4" ry="9"/><line x1="3" y1="12" x2="21" y2="12"/></svg>www.brightcoreliving.example</li>
      </ul>
    </div>
    <div class="brand">
      <span class="brand__dot"></span>
      <span class="brand__name">Brightcore Living</span>
    </div>
    <ul class="services">
      <li>Seminars</li><li>workshops</li><li>Coaching</li><li>podcasts</li>
    </ul>
  </section>

  <section class="card card--back">
    <div class="brand">
      <span class="brand__dot"></span>
      <span class="brand__name">Brightcore Living</span>
    </div>
    <p class="tagline">Your path to balance begins within</p>
  </section>
</body>
</html>
```